Maplecrest Disability - Social Security Disability Attorneys

Our company is expanding to attract clients nationwide for our social security disability practice. We have a logo, but I am looking for a creative and elegant letterhead that projects an image of being technologically advanced but still professional enough for the legal field. I am looking for the "wow factor" combined with this is still professional enough for a law practice.

Requesting letterhead and business card design
Updates

Had to update and change the logo. The previous logo had a typo. Please send updates with the new logo for consideration. The letterhead and business cards should be professional enough to be used for a law firm. Thanks.

Industry/Entity Type

Law Practice, Law Firm, Healthcare Industry, Government

Colors

Designer to choose colors to be used in the design.

Requirements
Nice to have
• **Please create a vertical design for the business card**

```html
<!DOCTYPE html>
<html lang="en">
<head>
<meta charset="utf-8">
<title>Maplecrest Disability – Business Card</title>
<link rel="stylesheet" href="https://fonts.googleapis.com/css2?family=Montserrat:wght@400;500;600;700&display=swap">
<style>
  :root {
    --backdrop: #239ed9;
    --brand-blue: #536eb6;
    --brand-orange: #f48125;
    --ink: #1b1b1b;
    --card-light: #ebeaeb;
    --white: #ffffff;
  }
  * { margin: 0; padding: 0; box-sizing: border-box; }
  html, body { width: 1200px; height: 1128px; overflow: hidden; }
  body {
    background: var(--backdrop);
    font-family: "Montserrat", sans-serif;
    position: relative;
  }
  .card {
    position: absolute;
    top: 129px;
    width: 498px;
    height: 868px;
    border-radius: 36px;
    overflow: hidden;
  }
  .card-back { left: 70px; background: var(--brand-blue); color: var(--white); }
  .card-front { left: 633px; background: var(--card-light); }
  .card-art { position: absolute; inset: 0; width: 100%; height: 100%; }

  .brand { position: absolute; left: 0; right: 0; text-align: center; }
  .brand-dot {
    display: block; width: 18px; height: 18px; border-radius: 50%;
    background: var(--brand-orange); margin: 0 auto 18px;
  }
  .brand-name {
    font-weight: 600; font-size: 25px; letter-spacing: 3px;
    text-transform: uppercase; line-height: 1;
  }
  .brand-tagline {
    font-weight: 500; font-size: 8.5px; letter-spacing: 2.4px;
    text-transform: uppercase; margin-top: 9px;
  }
  .card-back .brand { top: 356px; }
  .card-front .brand { top: 75px; color: var(--brand-blue); }

  .sectors {
    position: absolute; top: 700px; left: 0; right: 0;
    text-align: center; font-weight: 500; font-size: 20px; line-height: 31px;
  }

  .person { position: absolute; top: 308px; left: 0; right: 0; text-align: center; }
  .person-name {
    color: var(--brand-orange); font-weight: 700; font-size: 29px; letter-spacing: 0.2px;
  }
  .person-role {
    display: flex; align-items: center; justify-content: center; gap: 6px;
    font-size: 21px; color: var(--ink); margin-top: 2px;
  }
  .person-role::before, .person-role::after {
    content: ""; width: 64px; height: 2px; background: var(--brand-orange);
  }
  .address {
    position: absolute; top: 447px; left: 0; right: 0; text-align: center;
    font-size: 19px; line-height: 29px; color: var(--ink); font-weight: 500;
  }
  .contact-icons {
    position: absolute; top: 548px; left: 0; right: 0;
    display: flex; justify-content: center; gap: 34px;
  }
  .contact-icons svg { width: 21px; height: 21px; }
  .contact-list {
    position: absolute; top: 604px; left: 0; right: 0; text-align: center;
    font-size: 19.5px; line-height: 32.5px; color: var(--ink); font-weight: 500;
  }
</style>
</head>
<body>

<section class="card card-back">
  <div class="brand">
    <span class="brand-dot"></span>
    <p class="brand-name">Maplecrest Disability</p>
    <p class="brand-tagline">Social Security Disability Attorneys</p>
  </div>
  <p class="sectors">Law Practice, Law Firm,<br>Healthcare Industry, Government</p>
</section>

<section class="card card-front">
  <svg class="card-art" viewBox="0 0 498 868" preserveAspectRatio="none" aria-hidden="true">
    <polygon points="100,0 498,0 498,150 310,300" fill="#e6e5e6"/>
    <polygon points="498,150 498,430 240,430 0,700 0,640" fill="#f2f2f3"/>
    <polygon points="498,430 498,868 0,868 0,700 240,430" fill="#f5f4f5"/>
    <polygon points="0,595 498,770 498,868 0,868" fill="#ececed"/>
    <polygon points="330,300 498,150 498,430 270,430" fill="#f7f7f8"/>
    <polygon points="498,640 200,740 498,868" fill="#eeedef"/>
    <path d="M0,818 C140,850 300,772 485,778 C330,790 160,862 0,848 Z" fill="var(--brand-orange)"/>
    <path d="M0,850 C160,866 320,790 498,797" fill="none" stroke="#d9d9db" stroke-width="3"/>
    <path d="M0,858 C165,876 330,796 498,802 L498,868 L0,868 Z" fill="var(--brand-blue)"/>
  </svg>

  <div class="brand">
    <span class="brand-dot"></span>
    <p class="brand-name">Maplecrest Disability</p>
    <p class="brand-tagline">Social Security Disability Attorneys</p>
  </div>

  <div class="person">
    <p class="person-name">DANIEL WHITFORD</p>
    <p class="person-role">Co-Founder</p>
  </div>

  <p class="address">Suite 4, level 18, Harbour<br>Street Sydney NSW 2000</p>

  <div class="contact-icons">
    <svg viewBox="0 0 24 24" aria-label="Phone"><path fill="#f48125" d="M6.6 10.8a15 15 0 0 0 6.6 6.6l2.2-2.2c.3-.3.7-.4 1-.2 1.1.4 2.3.6 3.6.6.6 0 1 .4 1 1V20c0 .6-.4 1-1 1A17 17 0 0 1 3 4c0-.6.4-1 1-1h3.5c.6 0 1 .4 1 1 0 1.3.2 2.5.6 3.6.1.3 0 .7-.2 1z"/></svg>
    <svg viewBox="0 0 24 24" aria-label="Email"><rect x="2" y="5" width="20" height="14" rx="1.5" fill="#f48125"/><path d="M2.5 6l9.5 7 9.5-7" fill="none" stroke="#fff" stroke-width="1.6"/></svg>
    <svg viewBox="0 0 24 24" aria-label="Website"><circle cx="12" cy="12" r="10" fill="#f48125"/><path d="M2 12h20M12 2c3 3 3 17 0 20M12 2c-3 3-3 17 0 20" fill="none" stroke="#fff" stroke-width="1.3"/></svg>
  </div>

  <p class="contact-list">555-014-2738<br>Info@maplecrestdisability.com<br>www.maplecrestdisability.com</p>
</section>

</body>
</html>
```